Onboarding Infographic/brochure

We are a small criminal defense firm looking to create some sort of infographic or brochure that we can onboard new clients with. We are currently sending it out via email but want something a bit cooler and fun to send to clients. The information is:

A Few Quick Rules

We are here to help each step of the way. While questions are never discouraged, this letter will answer some of the most common ones we get asked.

Communications

As a client, you should always be in the loop. While we will try to respond to questions as quickly as possible, sometimes we are unable to respond right away. Do not worry - we promise to get back to you soon. Some questions might take some time to research, and a correct answer is better than a quick one.

Appointments

One of the benefits of having an attorney is the ability to discuss your case outside of court, minus the stress and headaches. If you need an appointment, please contact the office.

Appointments must be scheduled in advance. We do not want you to make a special trip to the office only to learn that we are in court or otherwise unavailable.

Jail Visits

If your family member is currently in jail, we take that very seriously. We will visit your loved one and introduce ourselves. While the case is ongoing, we ask that a family member be designated a “contact” person so that messages can be relayed quickly. Never discuss the facts of the case over the phone with someone who is in jail. Jail calls are recorded and we have seen too many cases go south based on remarks made over recorded lines.

Police Reports and Discovery

We will do our best to provide you with copies of everything we receive on your case. Most information will be emailed, so please keep your email address up to date.

Changes in Contact Information

If you move or change numbers during the case, please let us know. It is difficult to help if we are unable to reach you, and helping you is why we are here.

Court Appearances

Cases do not get resolved as quickly as they do on television. Expect there to be several hearings in your case and it may be necessary for you to attend one or more of them. If a hearing is set, you will receive notice of the date and time of each hearing.

Billing and Collections

We understand that this investment was a huge decision for you. As we focus on providing the best representation, we will need for you to stay on schedule with any payment arrangements agreed to at the time of your initial consultation.

Again, thank you for your trust in us. We look forward to getting a fantastic outcome on your case.

Target Market(s)

Criminal defense clients and their families

Industry/Entity Type

Legal

Font styles to use
Serif

Requirements
Must have
• Must incorporate all of the rules we email out. Would like diagrams, images or pictures
Nice to have
• We attached a Welcome brochure. Not sure I want it to look super similar, hence the request for infographic.

```html
<!DOCTYPE html>
<html lang="en">
<head>
<meta charset="UTF-8">
<title>A Few Quick Rules – Harlow Legal Group</title>
<link href="https://fonts.googleapis.com/css2?family=Montserrat:wght@400;500;800;900&display=swap" rel="stylesheet">
<style>
  :root {
    --sky: #dff0fa;
    --blue: #2596d4;
    --band: #2f6bb3;
    --dark: #232323;
    --ink: #222222;
    --white: #ffffff;
    --ring: #b9e0f5;
    --grey-top: #ffffff;
    --grey-bottom: #e3e3e3;
  }
  * { box-sizing: border-box; margin: 0; padding: 0; }
  html, body { width: 927px; height: 1200px; overflow: hidden; }
  body {
    position: relative;
    background: var(--sky);
    font-family: "Montserrat", Arial, sans-serif;
    color: var(--ink);
  }
  .header-bg { position: absolute; left: 0; top: 0; width: 927px; height: 260px; }
  .brand {
    position: absolute; top: 22px; left: 0; width: 927px;
    display: flex; justify-content: center; align-items: center; gap: 8px;
    font-weight: 800; font-size: 24px; letter-spacing: 0.5px; color: var(--ink);
  }
  .brand-mark { width: 16px; height: 16px; background: var(--blue); }
  .title {
    position: absolute; left: 27px; top: 70px;
    font-weight: 900; font-size: 49px; line-height: 44px; letter-spacing: 1px; color: var(--ink);
  }
  .intro {
    position: absolute; left: 414px; top: 80px; width: 480px;
    font-size: 14.3px; line-height: 22px; font-weight: 500; color: var(--ink);
  }
  .card {
    position: absolute; border-radius: 20px; color: var(--white);
  }
  .card--blue { background: var(--blue); }
  .card--dark { background: var(--dark); }
  .card h2 {
    font-weight: 900; font-size: 22px; line-height: 25px; letter-spacing: 0.6px;
    margin-bottom: 10px;
  }
  .card p { font-size: 11.8px; line-height: 18.2px; font-weight: 500; letter-spacing: 0.2px; }
  .card--left { padding: 24px 30px 0 51px; text-align: left; }
  .card--right { padding: 18px 58px 0 30px; text-align: right; }
  .icon {
    position: absolute; width: 88px; height: 88px; border-radius: 50%;
    background: var(--white); border: 6px solid var(--ring);
    display: flex; align-items: center; justify-content: center;
  }
  .icon-art { width: 46px; height: 46px; border-radius: 10px; }
  .arrow { position: absolute; }
  .footer {
    position: absolute; left: 0; top: 1076px; width: 927px; height: 124px;
    background: var(--band); color: var(--white);
    display: flex; align-items: center; justify-content: center; text-align: center;
    font-size: 24.5px; line-height: 31px; font-weight: 500; letter-spacing: 0.4px;
    padding: 0 30px;
  }
</style>
</head>
<body>
  <svg class="header-bg" viewBox="0 0 927 260" aria-hidden="true">
    <defs>
      <linearGradient id="headGrad" x1="0" y1="0" x2="0" y2="1">
        <stop offset="0" stop-color="#ffffff"/>
        <stop offset="1" stop-color="#e2e2e2"/>
      </linearGradient>
    </defs>
    <path d="M0 0 H927 V236 C720 190 360 168 0 188 Z" fill="url(#headGrad)"/>
    <path d="M0 188 C360 168 720 190 927 236 V256 C720 206 360 184 0 198 Z" fill="var(--blue)"/>
    <path d="M18 196 H45 V225 H62 L40 250 L18 225 Z" fill="var(--blue)" transform="translate(-5,0)"/>
  </svg>

  <div class="brand"><span class="brand-mark"></span>HARLOW LEGAL GROUP</div>
  <h1 class="title">A FEW QUICK<br>RULES</h1>
  <p class="intro">We are here to help each step of the way. While questions are never discouraged, this letter will answer some of the most common ones we get asked.</p>

  <section class="card card--blue card--left" style="left:52px;top:253px;width:394px;height:207px;">
    <h2>COMMUNICATIONS</h2>
    <p>As a client, you should always be in the loop. While we will try to respond to questions as quickly as possible, sometimes we are unable to respond right away. Do not worry - we promise to get back to you soon. Some questions might take some time to research, and a correct answer is better than a quick one.</p>
  </section>

  <section class="card card--dark card--right" style="left:481px;top:253px;width:394px;height:207px;">
    <h2>APPOINTMENTS</h2>
    <p>One of the benefits of having an attorney is the ability to discuss your case outside of court, minus the stress and headaches. If you need an appointment, please contact the office. Appointments must be scheduled in advance. We do not want you to make a special trip to the office only to learn that we are in court or otherwise unavailable.</p>
  </section>

  <section class="card card--blue card--right" style="left:16px;top:486px;width:859px;height:159px;padding-top:28px;">
    <h2>JAIL VISITS</h2>
    <p>If your family member is currently in jail, we take that very seriously. We will visit your loved one and introduce ourselves. While the case is ongoing, we ask that a family member be designated a “contact” person so that messages can be relayed quickly. Never discuss the facts of the case over the phone with someone who is in jail. Jail calls are recorded and we have seen too many cases go south based on remarks made over recorded lines.</p>
  </section>

  <section class="card card--dark card--left" style="left:52px;top:671px;width:394px;height:171px;padding-top:25px;">
    <h2>POLICE REPORTS AND DISCOVERY</h2>
    <p>We will do our best to provide you with copies of everything we receive on your case. Most information will be emailed, so please keep your email address up to date.</p>
  </section>

  <section class="card card--blue card--right" style="left:481px;top:671px;width:394px;height:171px;padding-top:20px;">
    <h2>CHANGES IN CONTACT INFORMATION</h2>
    <p>If you move or change numbers during the case, please let us know. It is difficult to help if we are unable to reach you, and helping you is why we are here.</p>
  </section>

  <section class="card card--blue card--left" style="left:52px;top:867px;width:394px;height:171px;padding-top:20px;">
    <h2>BILLING &amp; COLLECTIONS</h2>
    <p>We understand that this investment was a huge decision for you. As we focus on providing the best representation, we will need for you to stay on schedule with any payment arrangements agreed to at the time of your initial consultation.</p>
  </section>

  <section class="card card--dark card--right" style="left:481px;top:867px;width:394px;height:171px;padding-top:20px;">
    <h2>COURT APPEARANCES</h2>
    <p>Cases do not get resolved as quickly as they do on television. Expect there to be several hearings in your case and it may be necessary for you to attend one or more of them. If a hearing is set, you will receive notice of the date and time of each hearing.</p>
  </section>

  <div class="icon" style="left:8px;top:312px;"><div class="icon-art" role="img" aria-label="Megaphone illustration" style="background:linear-gradient(135deg,#f6b64a,#e8503a);"></div></div>
  <div class="icon" style="left:831px;top:320px;"><div class="icon-art" role="img" aria-label="Calendar with clock illustration" style="background:linear-gradient(135deg,#f27a6a,#5aa9e0);"></div></div>
  <div class="icon" style="left:831px;top:522px;"><div class="icon-art" role="img" aria-label="Jail cell bars illustration" style="background:linear-gradient(135deg,#5c5f66,#e0525a);"></div></div>
  <div class="icon" style="left:8px;top:712px;"><div class="icon-art" role="img" aria-label="Police report document illustration" style="background:linear-gradient(135deg,#cfd6de,#4c8fd6);"></div></div>
  <div class="icon" style="left:831px;top:712px;"><div class="icon-art" role="img" aria-label="Phone contact card illustration" style="background:linear-gradient(135deg,#8fd3f0,#4fbf87);"></div></div>
  <div class="icon" style="left:8px;top:908px;"><div class="icon-art" role="img" aria-label="Invoice and bill illustration" style="background:linear-gradient(135deg,#f0c45a,#d9593d);"></div></div>
  <div class="icon" style="left:831px;top:908px;"><div class="icon-art" role="img" aria-label="Courthouse building illustration" style="background:linear-gradient(135deg,#9aa6b2,#5e6b78);"></div></div>

  <svg class="arrow" style="left:446px;top:333px;" width="56" height="46" viewBox="0 0 56 46" aria-hidden="true"><path d="M0 13 H24 V0 L56 23 L24 46 V33 H0 Z" fill="var(--blue)"/></svg>
  <svg class="arrow" style="left:720px;top:458px;" width="48" height="48" viewBox="0 0 48 48" aria-hidden="true"><path d="M14 0 H34 V18 H48 L24 48 L0 18 H14 Z" fill="var(--dark)"/></svg>
  <svg class="arrow" style="left:68px;top:643px;" width="48" height="48" viewBox="0 0 48 48" aria-hidden="true"><path d="M14 0 H34 V18 H48 L24 48 L0 18 H14 Z" fill="var(--blue)"/></svg>
  <svg class="arrow" style="left:446px;top:733px;" width="56" height="46" viewBox="0 0 56 46" aria-hidden="true"><path d="M0 13 H24 V0 L56 23 L24 46 V33 H0 Z" fill="var(--blue)"/></svg>
  <svg class="arrow" style="left:808px;top:840px;" width="48" height="48" viewBox="0 0 48 48" aria-hidden="true"><path d="M14 0 H34 V18 H48 L24 48 L0 18 H14 Z" fill="var(--dark)"/></svg>
  <svg class="arrow" style="left:425px;top:924px;" width="56" height="46" viewBox="0 0 56 46" aria-hidden="true"><path d="M56 13 H32 V0 L0 23 L32 46 V33 H56 Z" fill="var(--blue)"/></svg>

  <footer class="footer">Again, thank you for your trust in us. We look forward to getting a fantastic outcome on your case.</footer>
</body>
</html>
```